Ecommerce web site design for 80s Retro website

we need a website to sell retro gift boxes based around 80's movies, music and gaming
it needs to work with the cartlantic ecommerce provider
there would only be 3 basic gift boxes (music, movies and gaming) , but the packaging would be able to be chosen to match birthdays, Christmas etc.
Each themed box will also have three levels of pricing, classic, premium, ultimate.
the website should be themed around the same colour scheme and look as the logo.

Target Market(s)

People after retro presents and gifts so probably people in their 40s to 50s

Coding

Coded - Design and coding required

Number of Pages Required

1 page

Requirements
Must have
• A real retro look and feel with bright neon colours and some icons or symbols of things from the 80s like tunepods, joysticks, movies, music, gaming etc
Should not have
• A boring bland interface

```html
<!DOCTYPE html>
<html lang="en">
<head>
<meta charset="utf-8">
<title>Neon Attic – Retro Gift Boxes</title>
<link rel="stylesheet" href="https://fonts.googleapis.com/css2?family=Montserrat:wght@400;500;600;700&display=swap">
<style>
:root{
  --purple:#6b4fd3;
  --black:#0b0b0b;
  --ink:#1a1a1a;
  --muted:#555;
  --band:#f2f2f2;
  --white:#fff;
  --line:#222;
}
*{box-sizing:border-box;margin:0;padding:0}
html,body{width:672px;height:1200px;overflow:hidden;background:var(--white)}
body{position:relative;font-family:"Montserrat",sans-serif;color:var(--ink)}
.abs{position:absolute}
a{color:inherit;text-decoration:none}

.promo-bar{left:0;top:0;width:672px;height:19px;background:var(--purple);color:var(--white);font-size:6.5px;font-weight:500}
.promo-bar .bell{left:62px;top:4px}
.promo-bar .msg{left:80px;top:5.5px}
.promo-bar .close{left:603px;top:5px;font-size:7px;font-weight:600}

.top-nav{left:0;top:19px;width:672px;height:23px;background:var(--black);color:var(--white);font-size:7px;font-weight:600}
.top-nav .group{top:8px;display:flex;gap:10px;white-space:nowrap}
.top-nav .left{left:63px}
.top-nav .right{left:390px}
.checkout-btn{left:549px;top:3px;width:61px;height:18px;border-radius:4px;background:var(--purple);font-size:7px;display:flex;align-items:center;justify-content:center}

.brand{left:63px;top:56px;display:flex;align-items:center;gap:6px;font-size:15px;font-weight:700;color:var(--purple);letter-spacing:.5px}
.brand .mark{width:14px;height:14px;background:var(--purple)}
.locale{left:548px;top:46px;display:flex;align-items:center;gap:4px;font-size:7.5px;font-weight:600}
.locale .dot{width:15px;height:15px;border-radius:50%;background:#c9243f}
.locale .cur{font-weight:400;color:var(--muted)}
.search{left:558px;top:71px;font-size:8px;color:#333;display:flex;align-items:center;gap:8px}
.main-nav{top:91px;font-size:7.8px;font-weight:500;color:#222}
.main-nav.active{color:var(--purple);border-bottom:1.5px solid var(--purple);padding-bottom:3px}

.hero{left:0;top:105px;width:672px;height:310px;
  background:
    linear-gradient(180deg,rgba(255,255,255,0) 70%,rgba(120,100,80,.25) 100%),
    linear-gradient(100deg,#cdbfb1 0%,#d8ccbf 28%,#c2b3a3 44%,#9cc4bf 58%,#86bdb6 70%,#7cb3ac 80%,#e0674c 90%,#c9a98a 100%)}
.hero-title{left:62px;top:238px;width:213px;height:44px;background:rgba(60,60,60,.82);color:var(--white);font-size:29px;font-weight:600;letter-spacing:1px;line-height:44px}

.welcome{left:0;top:431px;width:672px;height:61px;background:var(--band);text-align:center}
.welcome h1{margin-top:13px;font-size:16px;font-weight:700}
.welcome p{margin-top:4px;font-size:7.5px}

.category{width:171px}
.category .pic{width:171px;height:161px;box-shadow:0 0 2px rgba(0,0,0,.2)}
.category .name{margin-top:13px;font-size:7.5px;letter-spacing:.3px;color:var(--ink)}
.category .shop{margin-top:6px;font-size:7.5px;font-weight:700;color:var(--purple)}
.category .shop u{text-decoration:underline}

.section-title{left:62px;top:760px;width:548px;display:flex;align-items:center;gap:8px;font-size:16px;font-weight:700}
.section-title span.rule{flex:1;height:1px;background:var(--line)}

.product{width:125px;top:808px}
.product .pic{width:125px;height:143px;box-shadow:0 0 2px rgba(0,0,0,.25)}
.product .meta{margin-top:11px;display:flex;justify-content:space-between;font-size:7.5px;line-height:11.5px;letter-spacing:.2px}
.product .price{font-weight:700;padding-right:3px}

.divider{left:62px;top:1018px;width:548px;height:1px;background:var(--line)}

.foot-col h3{font-size:10px;font-weight:600;letter-spacing:.3px}
.foot-col ul{list-style:none;margin-top:11px;font-size:6.4px;line-height:11.4px;font-weight:500}
.email-box{left:339px;top:1072px;width:125px;height:24px;border:1px solid #999;font-size:6.4px;color:#666;padding:8px 0 0 5px}
.email-box .go{position:absolute;right:6px;top:6px}
.social{width:18px;height:18px}
.contact{left:492px;top:1083px;font-size:6.4px;line-height:11.4px;font-weight:500}

.legal-bar{left:62px;top:1163px;width:548px;height:28px;background:var(--band)}
.legal-bar .copy{left:2px;top:11px;font-size:6.6px;font-weight:500}
.pay-list{right:16px;top:7px;display:flex;gap:2px}
.pay{height:13px;padding:0 2px;background:var(--white);border:.5px solid #ccc;font-size:4.6px;font-weight:600;color:#333;line-height:12px;white-space:nowrap}
</style>
</head>
<body>

<div class="abs promo-bar">
  <svg class="abs bell" width="9" height="11" viewBox="0 0 9 11"><path d="M4.5 1a3 3 0 0 1 3 3v3l1 1.5H0.5L1.5 7V4a3 3 0 0 1 3-3z" fill="none" stroke="#fff" stroke-width=".8"/><circle cx="4.5" cy="9.8" r=".9" fill="#fff"/></svg>
  <span class="abs msg">Use code FLASH20 at checkout for an additional 20% off your order</span>
  <span class="abs close">X</span>
</div>

<div class="abs top-nav">
  <span class="abs group left"><span>HOME</span><span>//</span><span>CONTACT US</span></span>
  <span class="abs group right"><span>YOUR ACCOUNT</span><span>//</span><span>WISHLIST</span><span>$0.00</span></span>
  <a class="abs checkout-btn">CHECKOUT</a>
</div>

<div class="abs brand"><span class="mark"></span>NEON ATTIC</div>
<div class="abs locale"><span class="dot"></span>USA <span class="cur">($)</span>
  <svg width="7" height="5" viewBox="0 0 7 5" style="margin-left:8px"><path d="M.5 .5 3.5 3.8 6.5 .5" fill="none" stroke="#111" stroke-width="1.1"/></svg>
</div>
<div class="abs search">Search..
  <svg width="10" height="10" viewBox="0 0 10 10"><circle cx="4" cy="4" r="3" fill="none" stroke="#111" stroke-width="1.3"/><path d="M6.2 6.2 9.3 9.3" stroke="#111" stroke-width="1.4"/></svg>
</div>
<a class="abs main-nav active" style="left:275px">HOME</a>
<a class="abs main-nav" style="left:319px">ABOUT US</a>
<a class="abs main-nav" style="left:380px">ACCESSORIES</a>
<a class="abs main-nav" style="left:453px">BRANDS</a>
<a class="abs main-nav" style="left:506px">GIFT VOUCHERS</a>
<a class="abs main-nav" style="left:588px">BLOG</a>

<div class="abs hero" role="img" aria-label="Vintage teal cassette radio with red, blue and yellow cassette tapes on a weathered wooden table"></div>
<div class="abs hero-title">NEON ATTIC</div>

<div class="abs welcome">
  <h1>WELCOME TO NEON ATTIC</h1>
  <p>Paerspiciatis unde omnisiste natus errorsit voluptatem</p>
</div>

<div class="abs category" style="left:62px;top:520px">
  <div class="pic" role="img" aria-label="Illustrated black video cassette on a pink and lilac sunburst" style="background:linear-gradient(150deg,#e99be8 0%,#f3d6f1 22%,#d9a6ea 40%,#4a4a4a 52%,#3a3a3a 70%,#c9b4e6 85%,#b9c3e8 100%)"></div>
  <p class="name">PAERSPICIATIS UNDEOMNISIS</p>
  <p class="shop"><u>SHOP NOW</u>&nbsp; ›</p>
</div>
<div class="abs category" style="left:250px;top:520px">
  <div class="pic" role="img" aria-label="Red retro film festival poster on a dark green background" style="background:linear-gradient(90deg,#1e2a2a 0%,#1e2a2a 18%,#cf3b2e 30%,#d4402f 70%,#1e2a2a 82%,#1e2a2a 100%)"></div>
  <p class="name">PAERSPICIATIS UNDEOMNISIS</p>
  <p class="shop"><u>SHOP NOW</u>&nbsp; ›</p>
</div>
<div class="abs category" style="left:438px;top:520px">
  <div class="pic" role="img" aria-label="Yellow handheld game console on a pale cream background" style="background:linear-gradient(90deg,#f4f4ee 0%,#f1efdc 35%,#efd96a 50%,#f1efdc 65%,#f4f4ee 100%)"></div>
  <p class="name">PAERSPICIATIS UNDEOMNISIS</p>
  <p class="shop"><u>SHOP NOW</u>&nbsp; ›</p>
</div>

<div class="abs section-title"><span class="rule"></span>FEATURED PRODUCTS<span class="rule"></span></div>

<div class="abs product" style="left:62px">
  <div class="pic" role="img" aria-label="Grey handheld game console on white" style="background:linear-gradient(90deg,#fff 0%,#fff 22%,#d6d6d2 40%,#cfcfca 60%,#fff 78%,#fff 100%)"></div>
  <div class="meta"><span>PAERSPICIATIS UNDEO<br>MNISIS</span><span class="price">$ 40</span></div>
</div>
<div class="abs product" style="left:203px">
  <div class="pic" role="img" aria-label="Small black vintage portable television on white" style="background:linear-gradient(90deg,#fff 0%,#fff 10%,#3b4247 25%,#2a2e32 75%,#fff 90%,#fff 100%)"></div>
  <div class="meta"><span>PAERSPICIATIS UNDEO<br>MNISIS</span><span class="price">$ 40</span></div>
</div>
<div class="abs product" style="left:343px">
  <div class="pic" role="img" aria-label="Black audio cassette with rainbow stripes on white" style="background:linear-gradient(90deg,#fff 0%,#fff 10%,#2b2b2b 20%,#555 50%,#2b2b2b 80%,#fff 90%,#fff 100%)"></div>
  <div class="meta"><span>PAERSPICIATIS UNDEO<br>MNISIS</span><span class="price">$ 40</span></div>
</div>
<div class="abs product" style="left:484px">
  <div class="pic" role="img" aria-label="Copper coloured boombox on a mauve background" style="background:linear-gradient(180deg,#8e8088 0%,#9a8580 30%,#b5876b 55%,#a77e68 75%,#8d7f86 100%)"></div>
  <div class="meta"><span>PAERSPICIATIS UNDEO<br>MNISIS</span><span class="price">$ 40</span></div>
</div>

<div class="abs divider"></div>

<div class="abs foot-col" style="left:63px;top:1055px">
  <h3>QUICK LINKS</h3>
  <ul><li>HOME</li><li>ABOUT US</li><li>ACCESSORIES</li><li>BRANDS</li><li>GIFT VOUCHERS</li><li>BLOG</li></ul>
</div>
<div class="abs foot-col" style="left:169px;top:1055px">
  <h3>CUSTOMER INFORMATION</h3>
  <ul><li>FREQUENTLY ASKED QUESTIONS</li><li>CONTACT US</li><li>PRIVACY POLICY</li><li>TERMS &amp; CONDITIONS</li><li>DELIVERY INFORMATION</li><li>REFUNDS &amp; RETURNS</li></ul>
</div>
<div class="abs foot-col" style="left:339px;top:1055px"><h3>CONNECT WITH US</h3></div>
<div class="abs email-box">ENTER YOU EMAIL ADDRESS
  <svg class="go" width="6" height="9" viewBox="0 0 6 9"><path d="M1 1 4.5 4.5 1 8" fill="none" stroke="#333" stroke-width="1"/></svg>
</div>
<div class="abs social" style="left:339px;top:1104px;background:#3b5a98" aria-label="Facenet"></div>
<div class="abs social" style="left:361px;top:1104px;background:#2aa3e0" aria-label="Chirper"></div>
<div class="abs social" style="left:382px;top:1104px;background:#1d76b3" aria-label="Linkwork"></div>
<div class="abs social" style="left:404px;top:1104px;background:#d6213a" aria-label="Pinboard"></div>
<div class="abs social" style="left:426px;top:1104px;background:#e5322c" aria-label="Vidstream"></div>
<div class="abs social" style="left:339px;top:1126px;background:#6e4a3c" aria-label="Snapgram"></div>

<div class="abs foot-col" style="left:491px;top:1055px"><h3>GET IN TOUCH</h3></div>
<div class="abs contact">
  UNIT 8, 42 ARCADE LANE, BRIGHTWELL,<br>BW4 2NA<br>
  <span style="display:block;margin-top:3px">T: 0300 555 0198</span>
  <span style="display:block;margin-top:2px">E: hello@neonattic.shop</span>
</div>

<div class="abs legal-bar">
  <span class="abs copy">©2022. ALL RIGHTS RESERVED.</span>
  <div class="abs pay-list">
    <span class="pay">PayLoop</span>
    <span class="pay">OrbitCard</span>
    <span class="pay">Vantix</span>
    <span class="pay">Roamr</span>
    <span class="pay">Amerifly</span>
    <span class="pay">Kora</span>
    <span class="pay">Cardia</span>
    <span class="pay">PayLoop</span>
  </div>
</div>

</body>
</html>
```